KAJU Freightways #ALLKAJU Business Cards & Letterhead

I am looking to business cards designed for our organization. We are currently undergoing a small re-branding that is taking place. Our organization is called KAJU Freightways and we are headquartered in Phoenix, AZ. We primarily provide transportation and logistics services to the Marlow Parcel Bureau who is our largest customer. I would like to see a design that incorporates name, title, contact info, website, and address (this will be different depending on the employee). I would also like to see some color on the business card using our logo colors or a variation. I would like our logo on the back of the business card with the website displayed. The final design should communicate that we are a next generation transportation operate that focuses on being driver-first, customer-centric, innovative, and sustainable.We would also like our #ALLKAJU catch phrase incorporated as well.

Target Market(s)

Transportation & Logistics

Industry/Entity Type

Trucking Company

Contact Information for Business Card

-First and Last Name
-Position Title
-Contact Phone
-Contact Email
-Physical Address

Font styles to use
Serif

Colors

Designer to choose colors to be used in the design.

Requirements
Must have
• -KAJU logo prominently displayed
• -#ALLKAJU catch phrase used
• -Some amount of color, design gradient, etc.
• -Logo on the back with website listed (https://www.kajufreightco.example)

```html
<!DOCTYPE html>
<html lang="en">
<head>
<meta charset="utf-8">
<title>KAJU Freightways Stationery</title>
<link href="https://fonts.googleapis.com/css2?family=Lato:wght@400;700&family=Arimo:wght@400;700&display=swap" rel="stylesheet">
<style>
  :root {
    --teal: #143a45;
    --green: #79bb43;
    --paper: #f5f5f5;
    --ink: #1b1b1b;
    --backdrop: #e2e3e4;
    --sig: #d9dcdd;
  }
  * { margin: 0; padding: 0; box-sizing: border-box; }
  html, body { width: 1200px; height: 1200px; overflow: hidden; }
  body { background: var(--backdrop); font-family: 'Lato', sans-serif; }
  .stage { position: relative; width: 1200px; height: 1200px; }

  .sheet { position: absolute; background: var(--paper); box-shadow: 1px 2px 4px rgba(0,0,0,.35); overflow: hidden; }
  .band { position: absolute; top: 0; bottom: 0; left: 0; background: var(--teal); }

  .brand-name { position: absolute; font-family: 'Lato', sans-serif; font-weight: 700; line-height: 1; }

  /* Letterhead */
  .letterhead { left: 98px; top: 163px; width: 668px; height: 864px; }
  .letterhead .band { width: 58px; }
  .letterhead .brand-name { left: 72px; top: 62px; font-size: 24px; color: var(--teal); }
  .tagline-vertical {
    position: absolute; left: 24px; top: 785px; writing-mode: vertical-rl;
    color: #fff; font-size: 9.5px; font-weight: 700; letter-spacing: .04em;
  }
  .tagline-vertical .hash { color: var(--green); }

  .letter-head-info { position: absolute; top: 57px; font-size: 9.3px; line-height: 11.8px; color: var(--teal); }
  .company-block { left: 309px; }
  .company-block strong { font-weight: 700; }
  .contact-block { left: 516px; }
  .contact-line { display: flex; align-items: center; gap: 3px; }
  .contact-line svg { width: 8px; height: 8px; flex: none; }

  .letter-body {
    position: absolute; left: 100px; top: 218px; width: 514px;
    font-family: 'Arimo', sans-serif; font-size: 9.8px; line-height: 13px; color: var(--ink);
    letter-spacing: -0.08px;
  }
  .letter-body p { margin-bottom: 13px; text-align: justify; }
  .letter-body .date { margin-bottom: 13px; }
  .letter-body .recipient { margin-bottom: 30px; text-align: left; }
  .letter-body .salutation { font-weight: 700; margin-bottom: 26px; }
  .letter-body .closing { margin-top: 29px; margin-bottom: 10px; }
  .signature-area { width: 136px; height: 22px; background: var(--sig); margin-bottom: 10px; }

  /* Business cards */
  .card-back { left: 825px; top: 284px; width: 275px; height: 158px; background: var(--teal); }
  .card-back .brand-name { left: 0; right: 0; top: 70px; text-align: center; color: #fff; font-size: 18px; }
  .card-back .site { position: absolute; left: 0; right: 0; top: 133px; text-align: center; color: #fff; font-size: 7.5px; letter-spacing: .06em; }
  .card-back .site .accent { color: var(--green); }

  .card-front { left: 825px; top: 465px; width: 275px; height: 158px; }
  .card-front .band { width: 55px; }
  .card-front .brand-name { left: 0; width: 55px; top: 71px; text-align: center; color: #fff; font-size: 14px; }
  .card-info { position: absolute; left: 108px; top: 28px; color: var(--teal); font-size: 7px; line-height: 9px; }
  .card-info .person { color: var(--green); font-weight: 700; font-size: 9px; letter-spacing: .02em; line-height: 11px; }
  .card-info .role { margin-bottom: 24px; }
  .card-info .firm { font-weight: 700; }
  .card-info .address { margin-bottom: 5px; }
  .card-info .contact-line svg { width: 6px; height: 6px; }
</style>
</head>
<body>
<main class="stage">

  <section class="sheet letterhead">
    <div class="band"></div>
    <div class="brand-name">KAJU</div>
    <div class="tagline-vertical"><span class="hash">#</span>ALLKAJU</div>

    <div class="letter-head-info company-block">
      <strong>KAJU Freightways &amp; Energy Services, Inc.</strong><br>
      4410 North Canyon Ridge Road<br>
      Glendale, AZ 85301
    </div>
    <div class="letter-head-info contact-block">
      <div class="contact-line">
        <svg viewBox="0 0 10 10"><path d="M2 0.5 L3.8 2.6 L2.9 3.8 Q4 6.2 6.2 7.1 L7.4 6.2 L9.5 8 L8.3 9.5 Q1 8.5 0.5 1.7Z" fill="var(--green)"/></svg>623-555-0148
      </div>
      <div class="contact-line">
        <svg viewBox="0 0 10 10"><rect x="0.7" y="2" width="8.6" height="6" fill="none" stroke="var(--green)"/><path d="M0.7 2 L5 5.5 L9.3 2" fill="none" stroke="var(--green)"/></svg>info@kajufreightco.example
      </div>
      <div class="contact-line">
        <svg viewBox="0 0 10 10"><circle cx="5" cy="5" r="4.3" fill="none" stroke="var(--green)"/><ellipse cx="5" cy="5" rx="1.8" ry="4.3" fill="none" stroke="var(--green)"/><path d="M0.7 5 H9.3" stroke="var(--green)"/></svg>www.kajufreightco.example
      </div>
    </div>

    <article class="letter-body">
      <p class="date">November 15, 2019</p>
      <p class="recipient">Mr. John Doe<br>President<br>AA Corporation<br>111 Street Name, Suite#<br>City, State, 12345</p>
      <p class="salutation">Dear Mr. John,</p>
      <p>Lorem ipsum dolor sit amet, consectetur adipiscing elit. Integer diam quam, egestas eu ultrices eu, suscipit ac sapien. Phasellus eu dui nisi. Nam et euismod diam, nec lobortis tortor. Donec et diam nulla. Aenean varius tincidunt convallis. Aliquam a tortor at lacus dictum aliquet. Nunc laoreet metus sapien, in scelerisque augue consectetur in.</p>
      <p>Fusce nec justo laoreet, egestas justo sed, aliquet sem. Pellentesque pharetra massa non orci bibendum semper. Pellentesque cursus eu lectus a consectetur. Nunc volutpat suscipit posuere. Vestibulum facilisis vel quam malesuada mattis. Nulla in mattis tellus. Maecenas tristique mauris vitae pharetra tincidunt. In ut ornare risus. Integer molestie vestibulum nisi, semper dapibus mi condimentum eu.</p>
      <p>Nullam sagittis elit libero, id fringilla est tincidunt eget. Donec in ipsum ultricies, consectetur quam vel, facilisis elit. Phasellus tincidunt congue risus vel luctus. Suspendisse ut mollis neque. Donec ornare orci in turpis vestibulum, in ultrices metus scelerisque. Pellentesque mattis mattis nunc, nec tincidunt lacus egestas id. Fusce facilisis sagittis neque sit amet vulputate. Aliquam ut eros lobortis tortor facilisis vehicula. Sed sed luctus leo, at laoreet sapien. Donec placerat adipiscing ligula non euismod. In lobortis pretium nisl id luctus.</p>
      <p>Integer gravida tincidunt nibh, scelerisque tincidunt turpis. Suspendisse potenti. Nunc hendrerit euismod lectus id elementum. Fusce vitae gravida velit, quis eleifend lectus. In imperdiet mauris eu dui viverra sagittis. Donec tempor dui diam, condimentum gravida lacus pretium a. Nullam fringilla augue quis arcu placerat scelerisque. Aliquam nec tincidunt augue, sit amet posuere ipsum.</p>
      <p class="closing">Sincerely Yours,</p>
      <div class="signature-area" role="img" aria-label="Handwritten signature of Rowan Halvers"></div>
      <p>Rowan Halvers<br>President</p>
    </article>
  </section>

  <section class="sheet card-back">
    <div class="brand-name">KAJU</div>
    <div class="site">www.<span class="accent">kajufreightco</span>.example</div>
  </section>

  <section class="sheet card-front">
    <div class="band"></div>
    <div class="brand-name">KAJU</div>
    <div class="card-info">
      <div class="person">ROWAN HALVERS</div>
      <div class="role">President</div>
      <div class="firm">KAJU Freightways &amp; Energy Services, Inc.</div>
      <div class="address">4410 North Canyon Ridge Road<br>Glendale, AZ 85301</div>
      <div class="contact-line">
        <svg viewBox="0 0 10 10"><path d="M2 0.5 L3.8 2.6 L2.9 3.8 Q4 6.2 6.2 7.1 L7.4 6.2 L9.5 8 L8.3 9.5 Q1 8.5 0.5 1.7Z" fill="var(--green)"/></svg>623-555-0148
      </div>
      <div class="contact-line">
        <svg viewBox="0 0 10 10"><rect x="0.7" y="2" width="8.6" height="6" fill="none" stroke="var(--green)"/><path d="M0.7 2 L5 5.5 L9.3 2" fill="none" stroke="var(--green)"/></svg>rowan@kajufreightco.example
      </div>
      <div class="contact-line">
        <svg viewBox="0 0 10 10"><circle cx="5" cy="5" r="4.3" fill="none" stroke="var(--green)"/><ellipse cx="5" cy="5" rx="1.8" ry="4.3" fill="none" stroke="var(--green)"/><path d="M0.7 5 H9.3" stroke="var(--green)"/></svg>www.kajufreightco.example
      </div>
    </div>
  </section>

</main>
</body>
</html>
```